Business card por a urban DJ, up scale audience target

Need a sober design, modern, conservative colors but i can consider some options, y play rnb, hip hop, EDM and top40.

Business card for contact and personal info, double sided, use logo attrached please; im 42 so i need a card acording to my age an target audience.

Target Market(s)

Adult people, up scale audience

Industry/Entity Type

Music Download

Contact Information for Business Card

Cel (318) 4207265518 www.lumadrift.com

Requirements
Must have
• open mind
Nice to have
• open mind
Should not have
• DJ

```html
<!DOCTYPE html>
<html lang="en">
<head>
<meta charset="utf-8">
<title>Luma — Business Card</title>
<link href="https://fonts.googleapis.com/css2?family=Jost:wght@300;400;500&display=swap" rel="stylesheet">
<style>
  :root {
    --backdrop: #e6e4e0;
    --card: #ffffff;
    --ink-dark: #3b3b3b;
    --ink-mid: #5a5a5a;
    --ink-soft: #8a8a8a;
  }
  html, body {
    margin: 0;
    width: 1200px;
    height: 950px;
    overflow: hidden;
    background: var(--backdrop);
    font-family: "Jost", sans-serif;
  }
  .canvas {
    width: 1200px;
    height: 950px;
    display: flex;
    align-items: center;
    justify-content: center;
  }
  .business-card {
    width: 1000px;
    height: 572px;
    background: var(--card);
    box-shadow: 0 10px 30px rgba(0,0,0,0.12);
    display: flex;
    align-items: center;
    box-sizing: border-box;
    padding: 60px 0 0 140px;
  }
  .identity {
    display: flex;
    align-items: flex-end;
    gap: 32px;
  }
  .brand-name {
    font-size: 112px;
    font-weight: 500;
    line-height: 0.74;
    letter-spacing: 2px;
    color: var(--ink-dark);
  }
  .details {
    display: flex;
    flex-direction: column;
    gap: 10px;
  }
  .person {
    font-size: 28px;
    font-weight: 500;
    line-height: 1;
    color: var(--ink-dark);
    text-transform: uppercase;
    letter-spacing: 0.5px;
    white-space: nowrap;
  }
  .person .role {
    font-weight: 400;
    color: var(--ink-soft);
  }
  .contact {
    font-size: 21px;
    font-weight: 300;
    line-height: 1;
    color: var(--ink-mid);
    letter-spacing: 0.5px;
    white-space: nowrap;
  }
  .contact .divider {
    margin: 0 12px;
    color: var(--ink-soft);
  }
</style>
</head>
<body>
  <main class="canvas">
    <section class="business-card">
      <div class="identity">
        <div class="brand-name">LUMA</div>
        <div class="details">
          <div class="person">John Smith <span class="role">- CEO/Founder</span></div>
          <div class="contact">(318) 4207265518<span class="divider">|</span>www.lumadrift.com</div>
        </div>
      </div>
    </section>
  </main>
</body>
</html>
```